Business Card - connecting 2 souls and beggining the journey of self discovery

Logo on the front
with tag line

On the back list of services and contact details

Seminars
workshops
Coaching
podcasts

Darren Whitlow
Health & Wellbeing Life Coach
0491 372 615
darren@brightcoreliving.example
brightcoreliving.example

Industry/Entity Type

Life Coaching

Contact Information for Business Card

I like the use of colour from the logo to be used. I'm not a fan of white.

Requirements
Must have
• My tagline: The journey home starts with you
Nice to have
• Use of colour that is in the Brightcore Living logo

```html
<!DOCTYPE html>
<html lang="en">
<head>
<meta charset="utf-8">
<title>Brightcore Living – Business Card</title>
<link href="https://fonts.googleapis.com/css2?family=Lexend:wght@400;500;600&display=swap" rel="stylesheet">
<style>
  :root{
    --bg:#e9e7e4;
    --card-warm:#fde9dc;
    --card-cool:#efe4f6;
    --ink:#2b2b2b;
    --blue:#1f78c8;
    --blue-dark:#1766ad;
    --charcoal:#3e3e40;
    --brand-dot:#e8763a;
  }
  *{box-sizing:border-box;margin:0;padding:0}
  html,body{width:1200px;height:801px;overflow:hidden}
  body{background:var(--bg);font-family:"Lexend",sans-serif;color:var(--ink);position:relative}
  .card{position:absolute;top:246px;width:540px;height:309px;background:linear-gradient(120deg,var(--card-warm),var(--card-cool));border-radius:22px;overflow:hidden;box-shadow:0 6px 18px rgba(0,0,0,.12)}
  .card--front{left:40px}
  .card--back{left:620px}
  .card__bands{position:absolute;left:0;top:0;width:540px;height:309px}
  .brand{position:absolute;display:flex;align-items:center;gap:12px}
  .brand__mark{width:46px;height:46px;border-radius:50%;background:var(--brand-dot)}
  .brand__name{font-weight:600;font-size:22px;color:var(--ink)}
  .card--front .brand{left:0;right:0;top:80px;justify-content:center}
  .tagline{position:absolute;font-weight:500;font-size:17px;color:var(--ink)}
  .card--front .tagline{left:0;right:0;top:150px;text-align:center}
  .card--back .brand{left:34px;top:36px}
  .card--back .brand__name{font-size:17px}
  .card--back .tagline{left:34px;top:98px;width:240px;font-size:14px;line-height:19px}
  .services{position:absolute;left:40px;top:146px;display:grid;grid-template-columns:120px 120px;row-gap:8px;list-style:none;font-size:13px}
  .services li::before{content:"";display:inline-block;width:6px;height:6px;border-radius:50%;background:var(--blue);margin-right:8px;vertical-align:middle}
  .person{position:absolute;left:300px;top:36px}
  .person__name{font-size:22px;font-weight:600;color:var(--blue-dark)}
  .person__name span{color:var(--ink)}
  .person__role{font-size:12px;color:var(--blue);margin-top:2px}
  .contacts{position:absolute;left:300px;top:104px;list-style:none;font-size:11.5px}
  .contacts li{display:flex;align-items:center;gap:9px;margin-bottom:10px}
  .contacts svg{width:22px;height:22px;flex:none}
</style>
</head>
<body>

<section class="card card--front" aria-label="Card front">
  <svg class="card__bands" viewBox="0 0 540 309" aria-hidden="true">
    <path d="M300 270 L540 232 L540 254 L330 288 Z" fill="var(--blue)"/>
    <path d="M0 309 L0 278 L310 278 Q340 278 350 300 L354 309 Z" fill="var(--charcoal)"/>
  </svg>
  <div class="brand"><span class="brand__mark"></span><span class="brand__name">Brightcore Living</span></div>
  <p class="tagline">The journey home starts with you</p>
</section>

<section class="card card--back" aria-label="Card back">
  <svg class="card__bands" viewBox="0 0 540 309" aria-hidden="true">
    <path d="M0 309 L0 282 L320 282 L320 309 Z" fill="var(--charcoal)"/>
    <path d="M300 309 L300 268 Q300 240 335 236 L540 208 L540 309 Z" fill="var(--blue)"/>
  </svg>
  <div class="brand"><span class="brand__mark"></span><span class="brand__name">Brightcore Living</span></div>
  <p class="tagline">The journey home starts with you</p>
  <ul class="services">
    <li>Seminars</li><li>Coaching</li>
    <li>Workshops</li><li>Podcasts</li>
  </ul>
  <div class="person">
    <h1 class="person__name">Darren <span>Whitlow</span></h1>
    <p class="person__role">Health &amp; Wellbeing Life Coach</p>
  </div>
  <ul class="contacts">
    <li><svg viewBox="0 0 22 22"><circle cx="11" cy="11" r="11" fill="var(--blue)"/><path d="M7.5 6 L9.5 6 L10.3 8.6 L9 9.6 Q10 11.8 12.4 13 L13.4 11.7 L16 12.5 L16 14.5 Q15.5 15.8 14 15.6 Q7.2 14.6 6.4 8 Q6.3 6.4 7.5 6 Z" fill="#fff"/></svg>0491 372 615</li>
    <li><svg viewBox="0 0 22 22"><circle cx="11" cy="11" r="11" fill="var(--blue)"/><rect x="5.5" y="7" width="11" height="8" rx="1" fill="#fff"/><path d="M5.8 7.5 L11 11.6 L16.2 7.5" fill="none" stroke="var(--blue)" stroke-width="1.1"/></svg>darren@brightcoreliving.example</li>
    <li><svg viewBox="0 0 22 22"><circle cx="11" cy="11" r="11" fill="var(--blue)"/><circle cx="11" cy="11" r="5.5" fill="none" stroke="#fff" stroke-width="1.3"/><path d="M5.5 11 H16.5 M11 5.5 Q8 11 11 16.5 M11 5.5 Q14 11 11 16.5" fill="none" stroke="#fff" stroke-width="1"/></svg>www.brightcoreliving.example</li>
  </ul>
</section>

</body>
</html>
```